Accounting firm needing business card / letterhead designed
Marcus L. Trenholm, CPA
marcus@veltrowledger.com
www.veltrowledger.com
842 E Alder Ave Dunmere, WI 43827
555-562-0974

```html
<!DOCTYPE html>
<html lang="en">
<head>
<meta charset="utf-8">
<title>Veltrow Ledger – Business Card</title>
<link rel="stylesheet" href="https://fonts.googleapis.com/css2?family=Barlow+Semi+Condensed:wght@500;600&family=Open+Sans:wght@400&display=swap">
<style>
  :root {
    --navy: #21144b;
    --green: #5ba22b;
    --paper: #f7f7f7;
    --backdrop: #e6e6e6;
    --ink: #1e1e2a;
    --white: #ffffff;
  }
  * { margin: 0; padding: 0; box-sizing: border-box; }
  html, body { width: 1200px; height: 576px; overflow: hidden; }
  body {
    background: var(--backdrop);
    position: relative;
    font-family: "Open Sans", Arial, sans-serif;
  }
  .card {
    position: absolute;
    top: 138px;
    height: 294px;
    border-radius: 14px;
    overflow: hidden;
  }
  .card--front {
    left: 82px;
    width: 484px;
    background: var(--navy);
    display: flex;
    align-items: center;
    justify-content: center;
  }
  .card--back {
    left: 602px;
    width: 481px;
    background: var(--paper);
  }
  .brand-name {
    font-family: "Barlow Semi Condensed", Arial, sans-serif;
    font-weight: 600;
    text-transform: uppercase;
    letter-spacing: 0.06em;
    white-space: nowrap;
  }
  .card--front .brand-name {
    color: var(--white);
    font-size: 40px;
    margin-top: -10px;
  }
  .card--back .brand-name {
    position: absolute;
    left: 28px;
    top: 120px;
    width: 210px;
    text-align: center;
    color: var(--navy);
    font-size: 25px;
  }
  .contact {
    position: absolute;
    left: 268px;
    top: 77px;
    color: var(--ink);
    font-size: 13px;
    line-height: 18px;
  }
  .contact__name {
    font-family: "Barlow Semi Condensed", Arial, sans-serif;
    font-weight: 500;
    font-size: 19px;
    line-height: 22px;
    color: var(--navy);
  }
  .contact__title {
    color: var(--green);
    font-size: 11.5px;
    line-height: 16px;
    margin-bottom: 13px;
  }
  .contact__line {
    display: flex;
    align-items: center;
    gap: 10px;
    margin-top: 1px;
  }
  .contact__line svg { width: 12px; height: 10px; flex: none; }
  .footer-band {
    position: absolute;
    left: 0;
    bottom: 0;
    width: 481px;
    height: 34px;
  }
  .website {
    position: absolute;
    left: 268px;
    bottom: 10px;
    color: var(--white);
    font-size: 13px;
  }
</style>
</head>
<body>
  <section class="card card--front">
    <div class="brand-name">Veltrow Ledger</div>
  </section>

  <section class="card card--back">
    <div class="brand-name">Veltrow Ledger</div>

    <div class="contact">
      <div class="contact__name">Marcus L. Trenholm, CPA</div>
      <div class="contact__title">Director</div>
      <div class="contact__address">842 E Alder Ave Dunmere,<br>WI 43827</div>
      <div class="contact__line">
        <svg viewBox="0 0 12 10" aria-hidden="true"><path fill="#5ba22b" d="M1 3 Q6 -1 11 3 L9.5 4.5 L8 3.2 L4 3.2 L2.5 4.5 Z M3 5 L9 5 L10.5 9.5 L1.5 9.5 Z"/></svg>
        <span>555-562-0974</span>
      </div>
      <div class="contact__line">
        <svg viewBox="0 0 12 10" aria-hidden="true"><rect x="0.5" y="1" width="11" height="8" fill="#5ba22b"/><path d="M0.5 1 L6 5.5 L11.5 1" fill="none" stroke="#f7f7f7" stroke-width="1"/></svg>
        <span>marcus@veltrowledger.com</span>
      </div>
    </div>

    <svg class="footer-band" viewBox="0 0 481 34" aria-hidden="true">
      <rect x="0" y="18" width="240" height="16" fill="#5ba22b"/>
      <polygon points="238,0 481,0 481,34 224,34" fill="#21144b"/>
    </svg>
    <div class="website">www.veltrowledger.com</div>
  </section>
</body>
</html>
```